American cannabis tech company business card design

Pavrel.com is seeking a modern, professional, and brand-aligned business card that represents our company and its core values: Mission, Story, Values, and Impact. As an innovative cannabis company, we want a business card that is not only visually appealing but also serves as a representation of who we are and what we stand for.

Project Scope: Design a double-sided business card that integrates our brand identity and core values. Incorporate our key brand elements, ensuring a sleek and contemporary aesthetic. Visually reflect our core values (Mission, Story, Values, Impact) in a way that is engaging yet professional.

Target Market(s)

Vendors, third parties,

Contact Information for Business Card

Contact details (name, title, email, phone, website, etc.)

Font styles to use
Other font styles liked:
• Caslon, Centra

Colors

Designer to choose colors to be used in the design.

Requirements
Must have
• Pavrel.com logo and branding A creative yet clean way to integrate our core values (Mission, Story, Values, Impact) Modern typography and a well-structured layout
Nice to have
• forest green, grey, white, black
Should not have
• references to marijuana, leafs, plants, or related product

```html
<!DOCTYPE html>
<html lang="en">
<head>
<meta charset="utf-8">
<title>Pavrel.com Business Card</title>
<link rel="stylesheet" href="https://fonts.googleapis.com/css2?family=Poppins:wght@400;500;700;800&display=swap">
<style>
  :root {
    --forest: #1c3320;
    --cream: #fbf9f4;
    --paper: #ffffff;
    --ink: #141414;
    --backdrop: #e4e6e3;
  }
  * { margin: 0; padding: 0; box-sizing: border-box; }
  html, body {
    width: 1200px; height: 1200px; overflow: hidden;
    background: var(--backdrop);
    font-family: "Poppins", sans-serif;
  }
  .sheet {
    position: relative; width: 1200px; height: 1200px;
    display: flex; flex-direction: column; align-items: center;
    justify-content: center; gap: 60px;
  }
  .card {
    position: relative; width: 900px; height: 500px; overflow: hidden;
    box-shadow: 0 8px 24px rgba(0,0,0,0.18);
  }
  /* Front */
  .card--front { background: var(--forest); color: var(--cream); }
  .front-wordmark {
    position: absolute; top: 150px; left: 0; width: 100%;
    text-align: center; font-weight: 800; font-size: 120px;
    letter-spacing: 2px; line-height: 1;
  }
  .front-url {
    position: absolute; top: 380px; left: 0; width: 100%;
    text-align: center; font-weight: 500; font-size: 20px;
    letter-spacing: 6px;
  }
  /* Back */
  .card--back { background: var(--paper); color: var(--ink); }
  .back-wordmark {
    position: absolute; top: 50px; left: 50px;
    font-weight: 800; font-size: 82px; line-height: 1;
    color: var(--forest); letter-spacing: 1px;
  }
  .name-tab {
    position: absolute; top: 150px; right: 0; width: 380px; height: 100px;
    background: var(--forest); color: var(--paper);
    border-radius: 50px 0 0 50px;
    padding: 22px 0 0 70px;
  }
  .name-tab__name { font-weight: 700; font-size: 28px; letter-spacing: 1px; line-height: 1.1; }
  .name-tab__role { font-weight: 400; font-size: 20px; line-height: 1.1; }
  .contact-rule {
    position: absolute; top: 298px; left: 0; width: 100%; height: 5px;
    background: var(--forest);
  }
  .contact-item {
    position: absolute; top: 272px; width: 280px;
    display: flex; flex-direction: column; align-items: center;
  }
  .contact-item--phone { left: 20px; }
  .contact-item--mail { left: 310px; }
  .contact-item--web { left: 600px; }
  .contact-icon {
    width: 58px; height: 58px; border-radius: 50%;
    background: var(--forest);
    display: flex; align-items: center; justify-content: center;
  }
  .contact-text { margin-top: 18px; font-size: 24px; font-weight: 400; }
  .values-band {
    position: absolute; left: 0; bottom: 0; width: 100%; height: 100px;
    background: var(--forest); color: var(--cream);
    display: flex; align-items: center; justify-content: center;
    font-size: 22px; font-weight: 500; letter-spacing: 5px;
  }
</style>
</head>
<body>
<main class="sheet">
  <section class="card card--front" aria-label="Card front">
    <div class="front-wordmark">PAVREL</div>
    <div class="front-url">www.PAVREL.com</div>
  </section>

  <section class="card card--back" aria-label="Card back">
    <div class="back-wordmark">PAVREL</div>
    <div class="name-tab">
      <div class="name-tab__name">JONAH R. ELLERY</div>
      <div class="name-tab__role">Director</div>
    </div>

    <div class="contact-rule"></div>

    <div class="contact-item contact-item--phone">
      <div class="contact-icon">
        <svg width="30" height="30" viewBox="0 0 24 24" aria-hidden="true">
          <path fill="#ffffff" d="M6.6 10.8a15.1 15.1 0 0 0 6.6 6.6l2.2-2.2a1 1 0 0 1 1-.25 11.4 11.4 0 0 0 3.6.57 1 1 0 0 1 1 1V20a1 1 0 0 1-1 1A17 17 0 0 1 3 4a1 1 0 0 1 1-1h3.5a1 1 0 0 1 1 1c0 1.25.2 2.45.57 3.6a1 1 0 0 1-.25 1z"/>
        </svg>
      </div>
      <div class="contact-text">+1 405-555-0187</div>
    </div>

    <div class="contact-item contact-item--mail">
      <div class="contact-icon">
        <svg width="30" height="30" viewBox="0 0 24 24" aria-hidden="true">
          <rect x="3" y="6" width="18" height="12" fill="#ffffff"/>
          <path d="M3 6l9 7 9-7" fill="none" stroke="#1c3320" stroke-width="1.5"/>
        </svg>
      </div>
      <div class="contact-text">team@pavrel.com</div>
    </div>

    <div class="contact-item contact-item--web">
      <div class="contact-icon">
        <svg width="32" height="32" viewBox="0 0 24 24" aria-hidden="true">
          <g fill="none" stroke="#ffffff" stroke-width="1.4">
            <circle cx="12" cy="12" r="8.5"/>
            <ellipse cx="12" cy="12" rx="4" ry="8.5"/>
            <line x1="3.5" y1="12" x2="20.5" y2="12"/>
            <line x1="12" y1="3.5" x2="12" y2="20.5"/>
            <path d="M5 7.5h14M5 16.5h14"/>
          </g>
        </svg>
      </div>
      <div class="contact-text">www.PAVREL.com</div>
    </div>

    <div class="values-band">Mission | Story | Values and Impact</div>
  </section>
</main>
</body>
</html>
```